KRT Project Signage

Need a sign to be displayed in the front of properties currently under Construction or Renovation to advertise our company information. Need it to be Professional and Contemporary. We are a Design/Build Construction Company. Information should include Company Name, email, website, phone number. Attached: Logo and company brochure, also included and inspiration images

```html
<!DOCTYPE html>
<html lang="en">
<head>
<meta charset="utf-8">
<title>KRT Construction – Project Sign</title>
<link rel="stylesheet" href="https://fonts.googleapis.com/css2?family=Montserrat:wght@500;600;700;800&display=swap">
<style>
  :root {
    --backdrop: #e5e5e5;
    --charcoal: #333333;
    --ink: #262626;
    --paper: #ffffff;
    --accent: #f2e93f;
  }
  * { margin: 0; padding: 0; box-sizing: border-box; }
  html, body {
    width: 1200px; height: 1200px; overflow: hidden;
    background: var(--backdrop);
    font-family: "Montserrat", Arial, sans-serif;
  }
  .sign {
    position: absolute; left: 234px; top: 70px;
    width: 732px; height: 1060px;
    background: var(--charcoal);
    box-shadow: 4px 4px 6px rgba(0,0,0,0.25);
  }
  .brand-panel {
    position: absolute; left: 8px; top: 8px;
    width: 716px; height: 308px;
    background: var(--paper);
    display: flex; align-items: center; justify-content: center; gap: 16px;
  }
  .brand-mark {
    width: 44px; height: 44px; border-radius: 50%;
    background: var(--accent);
  }
  .brand-name {
    font-weight: 600; font-size: 46px; letter-spacing: 1px;
    color: var(--ink);
  }
  .service-band {
    position: absolute; left: 0; top: 316px; width: 732px; height: 124px;
    display: flex; align-items: center; justify-content: center;
    color: var(--paper);
    font-weight: 600; font-size: 62px; letter-spacing: 4px;
  }
  .contact-panel {
    position: absolute; left: 8px; top: 440px;
    width: 716px; height: 537px;
    background: var(--paper);
    text-align: center; color: var(--charcoal);
  }
  .icon {
    position: absolute; left: 50%; transform: translateX(-50%);
    border-radius: 50%; background: var(--charcoal);
  }
  .icon svg { width: 100%; height: 100%; display: block; }
  .icon-phone { top: 36px; width: 78px; height: 78px; }
  .icon-mail { top: 209px; width: 72px; height: 72px; }
  .icon-pin { top: 351px; width: 70px; height: 70px; }
  .phone {
    position: absolute; left: 0; right: 0; top: 122px;
    font-weight: 800; font-size: 72px; letter-spacing: -1px;
    color: var(--ink); line-height: 1;
  }
  .email {
    position: absolute; left: 0; right: 0; top: 303px;
    font-weight: 700; font-size: 37px; line-height: 1;
  }
  .address {
    position: absolute; left: 0; right: 0; top: 432px;
    font-weight: 600; font-size: 32px; line-height: 37px;
  }
  .web-band {
    position: absolute; left: 0; top: 977px; width: 732px; height: 83px;
    display: flex; align-items: center; justify-content: center;
    color: var(--paper);
    font-weight: 600; font-size: 28px; letter-spacing: 2px;
  }
</style>
</head>
<body>
  <div class="sign">
    <header class="brand-panel">
      <span class="brand-mark"></span>
      <span class="brand-name">KRT CONSTRUCTION</span>
    </header>

    <div class="service-band">DESIGN-BUILD</div>

    <section class="contact-panel">
      <div class="icon icon-phone">
        <svg viewBox="0 0 100 100" aria-hidden="true">
          <path fill="#fff" d="M33 24c3-2 6-1 8 2l6 10c1 3 1 5-2 7l-4 3c3 7 8 13 15 17l3-4c2-3 5-3 7-1l9 7c3 2 3 5 1 8l-4 5c-3 3-8 3-13 1-15-7-26-19-32-34-2-5-1-10 2-13z"/>
        </svg>
      </div>
      <div class="phone">555-010-4827</div>

      <div class="icon icon-mail">
        <svg viewBox="0 0 100 100" aria-hidden="true">
          <rect x="22" y="31" width="56" height="38" fill="none" stroke="#fff" stroke-width="5"/>
          <path d="M23 33l27 21 27-21M23 68l20-18M77 68l-20-18" fill="none" stroke="#fff" stroke-width="4"/>
        </svg>
      </div>
      <div class="email">info@krtconstruction.com</div>

      <div class="icon icon-pin">
        <svg viewBox="0 0 100 100" aria-hidden="true">
          <path fill="#fff" d="M50 18c-14 0-24 10-24 23 0 10 8 20 24 41 16-21 24-31 24-41 0-13-10-23-24-23zm0 13a10 10 0 1 1 0 20 10 10 0 0 1 0-20z"/>
        </svg>
      </div>
      <div class="address">1450 Harbor View Dr. Ste. 310<br>Palm Crest, FL 33400</div>
    </section>

    <footer class="web-band">WWW.KRTCONSTRUCTION.COM</footer>
  </div>
</body>
</html>
```